stationary deign for trucking company

im a trucking company looking for a professional set of stationary designs i deliver goods from point a to b
Updates

When submitting stationary designs I need envelope design, letterhead, cards, I’d badge etc

Industry/Entity Type

Trucking Company

Requirements
Must have
• must have letter head, business card, envelope, fax sheet, id badge, folder, thank you card, notebook, invoice sheet.
Nice to have
• nice to have them all custom made (letterhead,envelope, business card, I’d badge etc
Should not have
• must not have prepaid sign want i unique design for items

```html
<!DOCTYPE html>
<html lang="en">
<head>
<meta charset="utf-8">
<title>Harrow Freight – Employee ID Badge</title>
<link rel="stylesheet" href="https://fonts.googleapis.com/css2?family=Arimo:wght@400;700&display=swap">
<style>
  :root {
    --brand-blue: #1a5ca8;
    --header-grey: #e6e7e8;
    --ink: #1a1a1a;
    --card-white: #ffffff;
    --page-bg: #f2f3f5;
  }
  * { margin: 0; padding: 0; box-sizing: border-box; }
  html, body {
    width: 1200px;
    height: 1200px;
    overflow: hidden;
    background: var(--page-bg);
    font-family: "Arimo", Arial, sans-serif;
  }
  .canvas {
    position: relative;
    width: 1200px;
    height: 1200px;
  }
  .id-badge {
    position: absolute;
    left: 254px;
    top: 53px;
    width: 640px;
    height: 1012px;
    background: var(--card-white);
    transform: scale(1.08);
    transform-origin: top left;
    overflow: hidden;
  }
  .badge-header {
    position: absolute;
    left: 92px;
    top: 0;
    width: 454px;
    height: 263px;
    background: var(--header-grey);
  }
  .brand {
    position: absolute;
    left: 0;
    top: 150px;
    width: 100%;
    display: flex;
    align-items: center;
    justify-content: center;
    gap: 18px;
  }
  .brand-mark {
    width: 34px;
    height: 34px;
    background: var(--brand-blue);
  }
  .brand-name {
    font-weight: 700;
    font-size: 40px;
    letter-spacing: 3px;
    color: var(--ink);
  }
  .photo-notch {
    position: absolute;
    left: 177px;
    top: 234px;
    width: 284px;
    height: 284px;
    border-radius: 50%;
    background: var(--card-white);
  }
  .photo {
    position: absolute;
    left: 199px;
    top: 256px;
    width: 240px;
    height: 240px;
    border-radius: 50%;
    background: var(--brand-blue);
  }
  .name-banner {
    position: absolute;
    left: 0;
    top: 514px;
    width: 100%;
    display: flex;
    justify-content: center;
    align-items: center;
    gap: 10px;
  }
  .name-banner svg { width: 25px; height: 48px; }
  .employee-name {
    font-weight: 700;
    font-size: 39px;
    color: var(--brand-blue);
    white-space: nowrap;
  }
  .designation {
    position: absolute;
    left: 0;
    top: 564px;
    width: 100%;
    text-align: center;
    font-size: 20px;
    color: var(--ink);
  }
  .details-divider {
    position: absolute;
    left: 338px;
    top: 624px;
    width: 3px;
    height: 310px;
    background: var(--brand-blue);
  }
  .details {
    position: absolute;
    left: 0;
    top: 0;
    width: 100%;
  }
  .detail-row {
    position: absolute;
    left: 0;
    height: 28px;
    width: 100%;
  }
  .detail-label {
    position: absolute;
    right: 304px;
    top: 0;
    height: 28px;
    background: var(--brand-blue);
    color: var(--card-white);
    font-weight: 700;
    font-size: 23px;
    line-height: 28px;
    text-align: right;
    padding-right: 10px;
  }
  .detail-value {
    position: absolute;
    left: 349px;
    top: 0;
    font-size: 16px;
    line-height: 28px;
    color: var(--ink);
  }
  .website {
    position: absolute;
    left: 0;
    top: 945px;
    width: 100%;
    text-align: center;
    font-size: 26px;
    color: var(--brand-blue);
  }
</style>
</head>
<body>
<div class="canvas">
  <div class="id-badge">
    <div class="badge-header">
      <div class="brand">
        <span class="brand-mark"></span>
        <span class="brand-name">HARROW FREIGHT</span>
      </div>
    </div>
    <div class="photo-notch"></div>
    <div class="photo" role="img" aria-label="Employee portrait photo"></div>

    <div class="name-banner">
      <svg viewBox="0 0 25 48" aria-hidden="true"><polygon points="25,0 25,48 0,24" fill="#1a5ca8"/></svg>
      <span class="employee-name">EMPLOYE NAME</span>
      <svg viewBox="0 0 25 48" aria-hidden="true"><polygon points="0,0 0,48 25,24" fill="#1a5ca8"/></svg>
    </div>
    <p class="designation">DESIGNATION</p>

    <div class="details-divider"></div>
    <div class="details">
      <div class="detail-row" style="top:656px"><span class="detail-label" style="width:95px">D.O.B</span><span class="detail-value">01.01.2019</span></div>
      <div class="detail-row" style="top:698px"><span class="detail-label" style="width:92px">Id No</span><span class="detail-value">012345</span></div>
      <div class="detail-row" style="top:741px"><span class="detail-label" style="width:172px">Joined Date</span><span class="detail-value">01.01.2017</span></div>
      <div class="detail-row" style="top:784px"><span class="detail-label" style="width:167px">Expiry Date</span><span class="detail-value">01.01.2022</span></div>
      <div class="detail-row" style="top:827px"><span class="detail-label" style="width:99px">Email</span><span class="detail-value">info@harrowfreight.com</span></div>
      <div class="detail-row" style="top:870px"><span class="detail-label" style="width:107px">Phone</span><span class="detail-value">000111222</span></div>
    </div>

    <p class="website">harrowfreight.com</p>
  </div>
</div>
</body>
</html>
```